We are a recruitment company based in Norwich/Cambridge England.
I have included our company logo which we want to remain the same.

What we are looking for is a new creative Business card which will really stand out!!

Contact Information for Business Card

Harriet Dunmore
email: Harriet@plavex.co.uk
Address: Brackwell House
Fenmoor Enterprise Park
Partridge Way
Norwich
QB9 3KX
Tel:01632 960418

```html
<!DOCTYPE html>
<html lang="en">
<head>
<meta charset="utf-8">
<title>Plavex Business Card</title>
<link href="https://fonts.googleapis.com/css2?family=Montserrat:wght@600;700&family=Open+Sans:wght@400;600;700&display=swap" rel="stylesheet">
<style>
  :root {
    --backdrop: #e4e3e1;
    --card-front: #ffffff;
    --card-back: #eeeeee;
    --green: #8cc63f;
    --grey: #87838a;
    --ink: #333333;
  }
  * { box-sizing: border-box; margin: 0; padding: 0; }
  html, body { width: 1200px; height: 900px; overflow: hidden; }
  body {
    position: relative;
    background: var(--backdrop);
    font-family: "Open Sans", Arial, sans-serif;
  }
  .card {
    position: absolute;
    overflow: hidden;
    box-shadow: 0 6px 18px rgba(0,0,0,0.12);
  }
  .card--front {
    left: 78px; top: 35px; width: 587px; height: 363px;
    background: var(--card-front);
  }
  .card--back {
    left: 388px; top: 505px; width: 567px; height: 352px;
    background: var(--card-back);
  }
  .holder-name {
    position: absolute; left: 40px; top: 48px;
    font-family: "Montserrat", Arial, sans-serif;
    font-weight: 700; font-size: 21px; letter-spacing: 0.2px;
  }
  .holder-name .first { color: var(--green); }
  .holder-name .last { color: var(--grey); }
  .holder-role {
    position: absolute; left: 40px; top: 72px;
    font-size: 15px; color: var(--ink);
  }
  .contact-list {
    position: absolute; left: 38px; top: 170px;
    list-style: none;
  }
  .contact-list li {
    display: flex; align-items: center; gap: 6px;
    font-size: 15px; line-height: 21.5px; color: var(--ink);
  }
  .contact-list svg { width: 13px; height: 13px; fill: var(--green); flex: none; }
  .address {
    position: absolute; left: 40px; top: 286px;
    font-size: 15px; line-height: 22px; color: var(--ink);
  }
  .accent-circle {
    position: absolute; left: 395px; top: -20px;
    width: 250px; height: 250px; border-radius: 50%;
    background: var(--green);
  }
  .brand {
    position: absolute; left: 88px; top: 122px;
    display: flex; align-items: center; gap: 18px;
  }
  .brand-dot {
    width: 100px; height: 100px; border-radius: 50%;
    background: var(--green);
  }
  .brand-name {
    font-family: "Montserrat", Arial, sans-serif;
    font-weight: 600; font-size: 58px; line-height: 1;
    color: var(--grey);
  }
  .brand-tagline {
    position: absolute; left: 238px; top: 214px;
    font-size: 11.5px; letter-spacing: 3px; color: var(--grey);
  }
  .web-address {
    position: absolute; left: 0; right: 0; top: 296px;
    text-align: center; font-weight: 700; font-size: 15px;
    color: var(--green);
  }
</style>
</head>
<body>
  <section class="card card--front">
    <div class="accent-circle"></div>
    <h1 class="holder-name"><span class="first">HARRIET</span> <span class="last">DUNMORE</span></h1>
    <p class="holder-role">Managing Director</p>
    <ul class="contact-list">
      <li><svg viewBox="0 0 16 16"><path d="M2 6c0-2 2-3 6-3s6 1 6 3l-3 1-1-2H6L5 7 2 6zM4 8h8l1 5H3l1-5z"/></svg>01632 960418</li>
      <li><svg viewBox="0 0 16 16"><path d="M4 1h8v14H4zM5.5 3v9h5V3z"/></svg>07700 900417</li>
      <li><svg viewBox="0 0 16 16"><path d="M3 6h10v8H3zM5 1h6v4H5zM5 8h2v2H5zm4 0h2v2H9z"/></svg>01632 960419</li>
      <li><svg viewBox="0 0 16 16"><path d="M1 3h14v10H1zM2 4l6 5 6-5z" fill-rule="evenodd"/></svg>Harriet@plavex.co.uk</li>
      <li><svg viewBox="0 0 16 16"><circle cx="8" cy="8" r="7"/></svg>www.plavex.co.uk</li>
    </ul>
    <p class="address">Brackwell House, Fenmoor Enterprise Park,<br>Partridge Way, Norwich, QB9 3KX</p>
  </section>

  <section class="card card--back">
    <div class="brand">
      <span class="brand-dot"></span>
      <span class="brand-name">Plavex</span>
    </div>
    <p class="brand-tagline">Technology Recruitment</p>
    <p class="web-address">www.plavex.co.uk</p>
  </section>
</body>
</html>
```